Annual Report Velomar 2025

Take a PowerPoint presentation and turn it into a info graphic type annual report, posters and flyers.

Annual report ideally no more than 8 pages.

Please use the colours and fonts in the attached brand guidelines.

We are looking for an infographic visually appealing piece.

```html
<!DOCTYPE html>
<html lang="en">
<head>
<meta charset="utf-8">
<title>Velomar 2026 Annual Report – Slide Suite</title>
<link href="https://fonts.googleapis.com/css2?family=Poppins:wght@400;500;600;700&display=swap" rel="stylesheet">
<style>
  :root{
    --navy:#1a3260;
    --green:#7cac3c;
    --light-green:#e6f4c6;
    --white:#ffffff;
    --ink:#1d2a44;
    --canvas:#a9a9a9;
    --card:#ebebeb;
    --teal:#a8dccf;
    --grid:#e4e4e4;
    --gray-line:#8c8c8c;
  }
  *{margin:0;padding:0;box-sizing:border-box}
  html,body{width:1200px;height:1187px;overflow:hidden}
  body{background:var(--canvas);font-family:"Poppins",Arial,sans-serif;position:relative;color:var(--ink)}
  .defs{position:absolute;width:0;height:0}
  .slide{position:absolute;width:325px;height:183px;overflow:hidden}
  .slide.navy{background:var(--navy);color:var(--white)}
  .slide.light{background:var(--white);color:var(--ink)}
  .col-1{left:84px}.col-2{left:437px}.col-3{left:791px}
  .row-1{top:70px}.row-2{top:285px}.row-3{top:501px}.row-4{top:718px}.row-5{top:934px}
  .layer{position:absolute;left:0;top:0;width:325px;height:183px}
  .abs{position:absolute}

  .brand{position:absolute;display:flex;align-items:center;font-weight:600;line-height:1}
  .brand-dot{border-radius:50%;background:currentColor;display:inline-block}
  .brand.cover{font-size:15px;gap:4px}
  .brand.cover .brand-dot{width:11px;height:11px}
  .brand.foot{font-size:6px;gap:2px;left:13px;top:166px}
  .brand.foot .brand-dot{width:5px;height:5px}
  .on-navy{color:var(--white)}
  .on-light{color:var(--navy)}

  .cover-title{position:absolute;left:17px;top:60px;font-weight:700;font-size:21.5px;line-height:23px;text-transform:uppercase}
  .cover-sub{position:absolute;left:17px;top:136px;font-weight:700;font-size:10px;color:var(--green)}
  .cover-url{position:absolute;left:17px;top:161px;font-size:5px;font-weight:500}
  .g{color:var(--green)}

  .heading{position:absolute;font-weight:600;font-size:10.5px;line-height:1}
  .body{position:absolute;font-size:3.35px;line-height:4.15px;text-align:justify}
  .body p+p{margin-top:4px}

  .toc-title{position:absolute;left:10px;top:20px;font-weight:600;font-size:14px;line-height:14px;color:var(--ink)}
  .toc-item{position:absolute;width:147px;height:19px;border-radius:2px;color:var(--white);padding:2px 6px}
  .toc-item.navy-bg{background:var(--navy)}
  .toc-item.green-bg{background:var(--green)}
  .toc-item b{display:block;font-size:4.6px;font-weight:500;line-height:6px}
  .toc-item small{display:block;font-size:3.2px;line-height:5px}
  .toc-item i{position:absolute;right:5px;top:6px;font-style:normal;font-size:3.8px}

  .ticks{position:absolute;left:14px;top:110px;display:grid;grid-template-columns:75px 75px;row-gap:5px;font-size:3.5px}
  .ticks span{display:flex;align-items:center;gap:2px}
  .ticks svg{width:4px;height:4px}

  .photo-box{position:absolute;border-radius:5px}
  .chart-label{position:absolute;left:13px;top:31px;font-size:6px;font-weight:500}
  .process-title{position:absolute;left:0;width:325px;top:27px;text-align:center;font-size:12px;font-weight:500;line-height:1}
  .process-title small{font-size:3.6px;letter-spacing:1.5px;vertical-align:4px;margin-left:2px;border-bottom:.5px solid currentColor;padding-bottom:1px}
</style>
</head>
<body>

<svg class="defs" aria-hidden="true">
  <defs>
    <linearGradient id="tone-warm" x1="0" y1="0" x2="1" y2="1"><stop offset="0" stop-color="#d9cfc2"/><stop offset=".5" stop-color="#8f8577"/><stop offset="1" stop-color="#4f5a3c"/></linearGradient>
    <linearGradient id="tone-desk" x1="0" y1="0" x2="1" y2="1"><stop offset="0" stop-color="#c7a884"/><stop offset=".5" stop-color="#e8e3da"/><stop offset="1" stop-color="#8d6a4c"/></linearGradient>
    <linearGradient id="tone-hands" x1="0" y1="0" x2="1" y2="1"><stop offset="0" stop-color="#3a4a6a"/><stop offset=".5" stop-color="#c8a08a"/><stop offset="1" stop-color="#6e4a3a"/></linearGradient>
    <linearGradient id="tone-screen" x1="0" y1="0" x2="1" y2="1"><stop offset="0" stop-color="#dcdcdc"/><stop offset=".45" stop-color="#1f2733"/><stop offset="1" stop-color="#4b3a30"/></linearGradient>
    <linearGradient id="tone-coins" x1="0" y1="0" x2="1" y2="0"><stop offset="0" stop-color="#6d5640"/><stop offset=".5" stop-color="#b58a62"/><stop offset="1" stop-color="#7a4d35"/></linearGradient>
  </defs>
</svg>

<!-- Cover – navy -->
<section class="slide navy col-1 row-1">
  <svg class="layer" viewBox="0 0 325 183" role="img" aria-label="Photo: senior couple reading together at home"><path d="M198 0 Q242 90 183 183 L325 183 L325 0Z" fill="url(#tone-warm)"/></svg>
  <svg class="layer" viewBox="0 0 325 183" aria-hidden="true"><path d="M194 0 Q238 90 179 183" fill="none" stroke="var(--green)" stroke-width="8"/></svg>
  <div class="brand cover on-navy" style="left:17px;top:18px"><span class="brand-dot"></span>Velomar</div>
  <h1 class="cover-title">Resilience<br><span class="g">Through</span><br>Partnership</h1>
  <div class="cover-sub">2026 ANNUAL REPORT</div>
  <div class="cover-url">www.velomar.ca</div>
</section>

<!-- Cover – white -->
<section class="slide light col-2 row-1">
  <svg class="layer" viewBox="0 0 325 183" role="img" aria-label="Photo: hands reviewing financial charts on a desk"><path d="M198 0 Q242 90 183 183 L325 183 L325 0Z" fill="url(#tone-desk)"/></svg>
  <svg class="layer" viewBox="0 0 325 183" aria-hidden="true"><path d="M194 0 Q238 90 179 183" fill="none" stroke="var(--green)" stroke-width="8"/></svg>
  <div class="brand cover on-light" style="left:17px;top:18px"><span class="brand-dot"></span>Velomar</div>
  <h1 class="cover-title" style="color:var(--navy)">Resilience<br><span class="g">Through</span><br>Partnership</h1>
  <div class="cover-sub">2026 ANNUAL REPORT</div>
  <div class="cover-url" style="color:var(--ink)">www.velomar.ca</div>
</section>

<!-- Cover – arch -->
<section class="slide navy col-3 row-1">
  <svg class="layer" viewBox="0 0 325 183" role="img" aria-label="Photo: pile of coins"><path d="M0 70 Q162 30 325 70 L325 140 Q162 45 0 140Z" fill="url(#tone-coins)"/></svg>
  <svg class="layer" viewBox="0 0 325 183" aria-hidden="true"><path d="M0 142 Q162 47 325 142" fill="none" stroke="var(--green)" stroke-width="3"/></svg>
  <div class="brand cover on-navy" style="left:117px;top:18px"><span class="brand-dot"></span>Velomar</div>
  <div class="abs" style="left:0;width:325px;top:112px;text-align:center;color:var(--green);font-size:8px;font-weight:500">2026 ANNUAL REPORT</div>
  <h1 class="abs" style="left:0;width:325px;top:121px;text-align:center;font-size:18px;line-height:18.5px;font-weight:700">RESILIENCE <span class="g">THROUGH</span><br>PARTNERSHIP</h1>
  <div class="abs" style="left:0;width:325px;top:165px;text-align:center;font-size:5px;font-weight:500">www.velomar.ca</div>
</section>

<!-- Table of contents -->
<section class="slide light col-1 row-2">
  <h2 class="toc-title">Table of<br><span class="g">Contents</span></h2>
  <div class="toc-item navy-bg" style="left:10px;top:64px"><b>Welcome Slide</b><small>Write a Short Summary for this Slide</small><i>01</i></div>
  <div class="toc-item green-bg" style="left:10px;top:89px"><b>About Us</b><small>Write a Short Summary for this Slide</small><i>02</i></div>
  <div class="toc-item navy-bg" style="left:10px;top:114px"><b>Mission &amp; Vision</b><small>Write a Short Summary for this Slide</small><i>03</i></div>
  <div class="toc-item green-bg" style="left:10px;top:139px"><b>Our History</b><small>Write a Short Summary for this Slide</small><i>04</i></div>
  <div class="toc-item navy-bg" style="left:166px;top:64px"><b>Pricing Slide</b><small>Write a Short Summary for this Slide</small><i>05</i></div>
  <div class="toc-item green-bg" style="left:166px;top:89px"><b>Our Infographics</b><small>Write a Short Summary for this Slide</small><i>06</i></div>
  <div class="toc-item navy-bg" style="left:166px;top:114px"><b>Client Reviews</b><small>Write a Short Summary for this Slide</small><i>07</i></div>
  <div class="toc-item green-bg" style="left:166px;top:139px"><b>Data &amp; Charts</b><small>Write a Short Summary for this Slide</small><i>08</i></div>
</section>

<!-- Text + photo right, white -->
<section class="slide light col-2 row-2">
  <svg class="layer" viewBox="0 0 325 183" role="img" aria-label="Photo: open hands holding coins and a note about change"><path d="M190 0 Q232 92 186 183 L325 183 L325 0Z" fill="url(#tone-hands)"/></svg>
  <svg class="layer" viewBox="0 0 325 183" aria-hidden="true"><path d="M186 0 Q228 92 182 183" fill="none" stroke="var(--green)" stroke-width="8"/></svg>
  <h2 class="heading" style="left:16px;top:13px;color:var(--ink)">Heading Goes Here</h2>
  <div class="body" style="left:16px;top:29px;width:143px">
    <p>Lorem ipsum dolor sit amet, consectetuer adipiscing elit, sed diam nonummy nibh euismod tincidunt ut laoreet dolore magna aliquam erat volutpat. Ut wisi enim ad minim veniam, quis nostrud exerci tation ullamcorper suscipit lobortis nisl ut aliquip ex ea commodo consequat. Duis autem vel eum iriure dolor in hendrerit in vulputate velit esse molestie consequat, vel illum dolore eu feugiat nulla facilisis at vero eros et accumsan et iusto odio dignissim qui blandit praesent luptatum zzril delenit augue duis dolore te feugait nulla facilisi.</p>
    <p>Lorem ipsum dolor sit amet, cons ectetuer adipiscing elit, sed diam nonummy nibh euismod tincidunt ut laoreet dolore magna aliquam erat volutpat. Ut wisi enim ad minim veniam, quis nostrud exerci tation ullamcorper suscipit lobortis nisl ut aliquip ex ea commodo consequat.</p>
    <p>Lorem ipsum dolor sit amet, cons ectetuer adipiscing elit, sed diam nonummy nibh euismod tincidunt ut laoreet dolore magna aliquam erat volutpat. Ut wisi enim ad minim veniam, quis nostrud exerci tation ullamcorper suscipit lobortis nisl ut aliquip ex ea commodo consequat.</p>
  </div>
  <div class="brand foot on-light" style="left:16px;top:165px">
    <span class="brand-dot"></span>Velomar</div>
</section>

<!-- Text + ticks, navy -->
<section class="slide navy col-3 row-2">
  <svg class="layer" viewBox="0 0 325 183" role="img" aria-label="Photo: person pointing a pen at stock charts on a laptop"><path d="M192 0 Q232 95 196 183 L325 183 L325 0Z" fill="url(#tone-screen)"/></svg>
  <svg class="layer" viewBox="0 0 325 183" aria-hidden="true"><path d="M188 0 Q228 95 192 183" fill="none" stroke="var(--green)" stroke-width="8"/></svg>
  <h2 class="heading g" style="left:14px;top:13px">Heading Goes Here</h2>
  <div class="body" style="left:14px;top:29px;width:164px">
    <p>Lorem ipsum dolor sit amet, consectetuer adipiscing elit, sed diam nonummy nibh euismod tincidunt ut laoreet dolore magna aliquam erat volutpat. Ut wisi enim ad minim veniam, quis nostrud exerci tation ullamcorper suscipit lobortis nisl ut aliquip ex ea commodo consequat. Duis autem vel eum iriure dolor in hendrerit in vulputate velit esse molestie consequat, vel illum dolore eu feugiat nulla facilisis at vero eros et accumsan et iusto odio dignissim qui blandit praesent luptatum zzril delenit augue duis dolore te feugait nulla facilisi.</p>
  </div>
  <h2 class="heading g" style="left:14px;top:92px">Heading Goes Here</h2>
  <div class="ticks">
    <span><svg viewBox="0 0 10 10"><circle cx="5" cy="5" r="4.3" fill="none" stroke="var(--green)" stroke-width="1.2"/><path d="M3 5.2l1.5 1.5L7.2 3.8" fill="none" stroke="var(--green)" stroke-width="1.2"/></svg>Lorem ipsum dolor sit amet</span>
    <span><svg viewBox="0 0 10 10"><circle cx="5" cy="5" r="4.3" fill="none" stroke="var(--green)" stroke-width="1.2"/><path d="M3 5.2l1.5 1.5L7.2 3.8" fill="none" stroke="var(--green)" stroke-width="1.2"/></svg>Lorem ipsum dolor sit amet</span>
    <span><svg viewBox="0 0 10 10"><circle cx="5" cy="5" r="4.3" fill="none" stroke="var(--green)" stroke-width="1.2"/><path d="M3 5.2l1.5 1.5L7.2 3.8" fill="none" stroke="var(--green)" stroke-width="1.2"/></svg>Lorem ipsum dolor sit amet</span>
    <span><svg viewBox="0 0 10 10"><circle cx="5" cy="5" r="4.3" fill="none" stroke="var(--green)" stroke-width="1.2"/><path d="M3 5.2l1.5 1.5L7.2 3.8" fill="none" stroke="var(--green)" stroke-width="1.2"/></svg>Lorem ipsum dolor sit amet</span>
    <span><svg viewBox="0 0 10 10"><circle cx="5" cy="5" r="4.3" fill="none" stroke="var(--green)" stroke-width="1.2"/><path d="M3 5.2l1.5 1.5L7.2 3.8" fill="none" stroke="var(--green)" stroke-width="1.2"/></svg>Lorem ipsum dolor sit amet</span>
    <span><svg viewBox="0 0 10 10"><circle cx="5" cy="5" r="4.3" fill="none" stroke="var(--green)" stroke-width="1.2"/><path d="M3 5.2l1.5 1.5L7.2 3.8" fill="none" stroke="var(--green)" stroke-width="1.2"/></svg>Lorem ipsum dolor sit amet</span>
    <span><svg viewBox="0 0 10 10"><circle cx="5" cy="5" r="4.3" fill="none" stroke="var(--green)" stroke-width="1.2"/><path d="M3 5.2l1.5 1.5L7.2 3.8" fill="none" stroke="var(--green)" stroke-width="1.2"/></svg>Lorem ipsum dolor sit amet</span>
    <span><svg viewBox="0 0 10 10"><circle cx="5" cy="5" r="4.3" fill="none" stroke="var(--green)" stroke-width="1.2"/><path d="M3 5.2l1.5 1.5L7.2 3.8" fill="none" stroke="var(--green)" stroke-width="1.2"/></svg>Lorem ipsum dolor sit amet</span>
  </div>
  <div class="brand foot on-navy" style="left:14px;top:165px"><span class="brand-dot"></span>Velomar</div>
</section>

<!-- Two columns, white -->
<section class="slide light col-1 row-3">
  <h2 class="heading" style="left:13px;top:13px;color:var(--ink)">Heading Goes Here</h2>
  <div class="body" style="left:13px;top:29px;width:142px">
    <p>Lorem ipsum dolor sit amet, consectetuer adipiscing elit, sed diam nonummy nibh euismod tincidunt ut laoreet dolore magna aliquam erat volutpat. Ut wisi enim ad minim veniam, quis nostrud exerci tation ullamcorper suscipit lobortis nisl ut aliquip ex ea commodo consequat. Duis autem vel eum iriure dolor in hendrerit in vulputate velit esse molestie consequat, vel illum dolore eu feugiat nulla facilisis at vero eros et accumsan et iusto odio dignissim qui blandit praesent luptatum zzril delenit augue duis dolore te feugait nulla facilisi.</p>
    <p>Lorem ipsum dolor sit amet, cons ectetuer adipiscing elit, sed diam nonummy nibh euismod tincidunt ut laoreet dolore magna aliquam erat volutpat. Ut wisi enim ad minim veniam, quis nostrud exerci tation ullamcorper suscipit lobortis nisl ut aliquip ex ea commodo consequat.</p>
    <p>Lorem ipsum dolor sit amet, cons ectetuer adipiscing elit, sed diam nonummy nibh euismod tincidunt ut laoreet dolore magna aliquam erat volutpat. Ut wisi enim ad minim veniam, quis nostrud exerci tation ullamcorper suscipit lobortis nisl ut aliquip ex ea commodo consequat.</p>
  </div>
  <div class="body" style="left:168px;top:29px;width:142px">
    <p>Lorem ipsum dolor sit amet, consectetuer adipiscing elit, sed diam nonummy nibh euismod tincidunt ut laoreet dolore magna aliquam erat volutpat. Ut wisi enim ad minim veniam, quis nostrud exerci tation ullamcorper suscipit lobortis nisl ut aliquip ex ea commodo consequat. Duis autem vel eum iriure dolor in hendrerit in vulputate velit esse molestie consequat, vel illum dolore eu feugiat nulla facilisis at vero eros et accumsan et iusto odio dignissim qui blandit praesent luptatum zzril delenit augue duis dolore te feugait nulla facilisi.</p>
    <p>Lorem ipsum dolor sit amet, cons ectetuer adipiscing elit, sed diam nonummy nibh euismod tincidunt ut laoreet dolore magna aliquam erat volutpat. Ut wisi enim ad minim veniam, quis nostrud exerci tation ullamcorper suscipit lobortis nisl ut aliquip ex ea commodo consequat.</p>
    <p>Lorem ipsum dolor sit amet, cons ectetuer adipiscing elit, sed diam nonummy nibh euismod tincidunt ut laoreet dolore magna aliquam erat volutpat. Ut wisi enim ad minim veniam, quis nostrud exerci tation ullamcorper suscipit lobortis nisl ut aliquip ex ea commodo consequat.</p>
  </div>
  <div class="brand foot on-light"><span class="brand-dot"></span>Velomar</div>
</section>

<!-- Photo left + text, navy -->
<section class="slide navy col-2 row-3">
  <svg class="layer" viewBox="0 0 325 183" role="img" aria-label="Photo: hand with pen pointing at market charts on a laptop"><path d="M0 0 L133 0 Q98 92 143 183 L0 183Z" fill="url(#tone-screen)"/></svg>
  <svg class="layer" viewBox="0 0 325 183" aria-hidden="true"><path d="M137 0 Q102 92 147 183" fill="none" stroke="var(--green)" stroke-width="8"/></svg>
  <h2 class="heading g" style="left:151px;top:13px">Heading Goes Here</h2>
  <div class="body" style="left:151px;top:29px;width:154px">
    <p>Lorem ipsum dolor sit amet, consectetuer adipiscing elit, sed diam nonummy nibh euismod tincidunt ut laoreet dolore magna aliquam erat volutpat. Ut wisi enim ad minim veniam, quis nostrud exerci tation ullamcorper suscipit lobortis nisl ut aliquip ex ea commodo consequat. Duis autem vel eum iriure dolor in hendrerit in vulputate velit esse molestie consequat, vel illum dolore eu feugiat nulla facilisis at vero eros et accumsan et iusto odio dignissim qui blandit praesent luptatum zzril delenit augue duis dolore te feugait nulla facilisi.</p>
    <p>Lorem ipsum dolor sit amet, cons ectetuer adipiscing elit, sed diam nonummy nibh euismod tincidunt ut laoreet dolore magna aliquam erat volutpat. Ut wisi enim ad minim veniam, quis nostrud exerci tation ullamcorper suscipit lobortis nisl ut aliquip ex ea commodo consequat.</p>
    <p>Lorem ipsum dolor sit amet, cons ectetuer adipiscing elit, sed diam nonummy nibh euismod tincidunt ut laoreet dolore magna aliquam erat volutpat. Ut wisi enim ad minim veniam, quis nostrud exerci tation ullamcorper suscipit lobortis nisl ut aliquip ex ea commodo consequat.</p>
  </div>
  <div class="brand foot on-navy" style="left:270px;top:164px"><span class="brand-dot"></span>Velomar</div>
</section>

<!-- Two columns, navy -->
<section class="slide navy col-3 row-3">
  <h2 class="heading g" style="left:13px;top:13px">Heading Goes Here</h2>
  <div class="body" style="left:13px;top:29px;width:142px">
    <p>Lorem ipsum dolor sit amet, consectetuer adipiscing elit, sed diam nonummy nibh euismod tincidunt ut laoreet dolore magna aliquam erat volutpat. Ut wisi enim ad minim veniam, quis nostrud exerci tation ullamcorper suscipit lobortis nisl ut aliquip ex ea commodo consequat. Duis autem vel eum iriure dolor in hendrerit in vulputate velit esse molestie consequat, vel illum dolore eu feugiat nulla facilisis at vero eros et accumsan et iusto odio dignissim qui blandit praesent luptatum zzril delenit augue duis dolore te feugait nulla facilisi.</p>
    <p>Lorem ipsum dolor sit amet, cons ectetuer adipiscing elit, sed diam nonummy nibh euismod tincidunt ut laoreet dolore magna aliquam erat volutpat. Ut wisi enim ad minim veniam, quis nostrud exerci tation ullamcorper suscipit lobortis nisl ut aliquip ex ea commodo consequat.</p>
    <p>Lorem ipsum dolor sit amet, cons ectetuer adipiscing elit, sed diam nonummy nibh euismod tincidunt ut laoreet dolore magna aliquam erat volutpat. Ut wisi enim ad minim veniam, quis nostrud exerci tation ullamcorper suscipit lobortis nisl ut aliquip ex ea commodo consequat.</p>
  </div>
  <div class="body" style="left:168px;top:29px;width:142px">
    <p>Lorem ipsum dolor sit amet, consectetuer adipiscing elit, sed diam nonummy nibh euismod tincidunt ut laoreet dolore magna aliquam erat volutpat. Ut wisi enim ad minim veniam, quis nostrud exerci tation ullamcorper suscipit lobortis nisl ut aliquip ex ea commodo consequat. Duis autem vel eum iriure dolor in hendrerit in vulputate velit esse molestie consequat, vel illum dolore eu feugiat nulla facilisis at vero eros et accumsan et iusto odio dignissim qui blandit praesent luptatum zzril delenit augue duis dolore te feugait nulla facilisi.</p>
    <p>Lorem ipsum dolor sit amet, cons ectetuer adipiscing elit, sed diam nonummy nibh euismod tincidunt ut laoreet dolore magna aliquam erat volutpat. Ut wisi enim ad minim veniam, quis nostrud exerci tation ullamcorper suscipit lobortis nisl ut aliquip ex ea commodo consequat.</p>
    <p>Lorem ipsum dolor sit amet, cons ectetuer adipiscing elit, sed diam nonummy nibh euismod tincidunt ut laoreet dolore magna aliquam erat volutpat. Ut wisi enim ad minim veniam, quis nostrud exerci tation ullamcorper suscipit lobortis nisl ut aliquip ex ea commodo consequat.</p>
  </div>
  <div class="brand foot on-navy"><span class="brand-dot"></span>Velomar</div>
</section>

<!-- Text + framed photo, navy -->
<section class="slide navy col-1 row-4">
  <h2 class="heading g" style="left:13px;top:13px">Heading Goes Here</h2>
  <div class="body" style="left:13px;top:29px;width:142px">
    <p>Lorem ipsum dolor sit amet, consectetuer adipiscing elit, sed diam nonummy nibh euismod tincidunt ut laoreet dolore magna aliquam erat volutpat. Ut wisi enim ad minim veniam, quis nostrud exerci tation ullamcorper suscipit lobortis nisl ut aliquip ex ea commodo consequat. Duis autem vel eum iriure dolor in hendrerit in vulputate velit esse molestie consequat, vel illum dolore eu feugiat nulla facilisis at vero eros et accumsan et iusto odio dignissim qui blandit praesent luptatum zzril delenit augue duis dolore te feugait nulla facilisi.</p>
    <p>Lorem ipsum dolor sit amet, cons ectetuer adipiscing elit, sed diam nonummy nibh euismod tincidunt ut laoreet dolore magna aliquam erat volutpat. Ut wisi enim ad minim veniam, quis nostrud exerci tation ullamcorper suscipit lobortis nisl ut aliquip ex ea commodo consequat.</p>
    <p>Lorem ipsum dolor sit amet, cons ectetuer adipiscing elit, sed diam nonummy nibh euismod tincidunt ut laoreet dolore magna aliquam erat volutpat. Ut wisi enim ad minim veniam, quis nostrud exerci tation ullamcorper suscipit lobortis nisl ut aliquip ex ea commodo consequat.</p>
  </div>
  <div class="photo-box" role="img" aria-label="Photo: analyst pointing at trading charts on a laptop" style="left:169px;top:30px;width:143px;height:120px;background:linear-gradient(135deg,#e4e4e4,#2a3240 55%,#4a3a30)"></div>
  <div class="brand foot on-navy"><span class="brand-dot"></span>Velomar</div>
</section>

<!-- Framed photo + text, white -->
<section class="slide light col-2 row-4">
  <h2 class="heading" style="left:13px;top:13px;color:var(--ink)">Heading Goes Here</h2>
  <div class="photo-box" role="img" aria-label="Photo: team reviewing printed financial charts on a desk" style="left:13px;top:30px;width:143px;height:120px;background:linear-gradient(135deg,#8d6a4c,#e8e3da 50%,#a5825f)"></div>
  <div class="body" style="left:168px;top:29px;width:142px">
    <p>Lorem ipsum dolor sit amet, consectetuer adipiscing elit, sed diam nonummy nibh euismod tincidunt ut laoreet dolore magna aliquam erat volutpat. Ut wisi enim ad minim veniam, quis nostrud exerci tation ullamcorper suscipit lobortis nisl ut aliquip ex ea commodo consequat. Duis autem vel eum iriure dolor in hendrerit in vulputate velit esse molestie consequat, vel illum dolore eu feugiat nulla facilisis at vero eros et accumsan et iusto odio dignissim qui blandit praesent luptatum zzril delenit augue duis dolore te feugait nulla facilisi.</p>
    <p>Lorem ipsum dolor sit amet, cons ectetuer adipiscing elit, sed diam nonummy nibh euismod tincidunt ut laoreet dolore magna aliquam erat volutpat. Ut wisi enim ad minim veniam, quis nostrud exerci tation ullamcorper suscipit lobortis nisl ut aliquip ex ea commodo consequat.</p>
    <p>Lorem ipsum dolor sit amet, cons ectetuer adipiscing elit, sed diam nonummy nibh euismod tincidunt ut laoreet dolore magna aliquam erat volutpat. Ut wisi enim ad minim veniam, quis nostrud exerci tation ullamcorper suscipit lobortis nisl ut aliquip ex ea commodo consequat.</p>
  </div>
  <div class="brand foot on-light"><span class="brand-dot"></span>Velomar</div>
</section>

<!-- Line chart -->
<section class="slide light col-3 row-4">
  <h2 class="heading" style="left:13px;top:13px;color:var(--ink)">Heading Goes Here</h2>
  <div class="chart-label">Line Chart</div>
  <svg class="layer" viewBox="0 0 325 183" role="img" aria-label="Line chart of monthly sales and orders">
    <g stroke="var(--grid)" stroke-width=".4">
      <line x1="20" x2="312" y1="42" y2="42"/><line x1="20" x2="312" y1="52" y2="52"/><line x1="20" x2="312" y1="62" y2="62"/><line x1="20" x2="312" y1="72" y2="72"/><line x1="20" x2="312" y1="82" y2="82"/><line x1="20" x2="312" y1="92" y2="92"/><line x1="20" x2="312" y1="102" y2="102"/><line x1="20" x2="312" y1="112" y2="112"/><line x1="20" x2="312" y1="122" y2="122"/><line x1="20" x2="312" y1="132" y2="132"/><line x1="20" x2="312" y1="142" y2="142"/>
      <line x1="44.3" x2="44.3" y1="42" y2="142"/><line x1="68.7" x2="68.7" y1="42" y2="142"/><line x1="93" x2="93" y1="42" y2="142"/><line x1="117.3" x2="117.3" y1="42" y2="142"/><line x1="141.7" x2="141.7" y1="42" y2="142"/><line x1="166" x2="166" y1="42" y2="142"/><line x1="190.3" x2="190.3" y1="42" y2="142"/><line x1="214.7" x2="214.7" y1="42" y2="142"/><line x1="239" x2="239" y1="42" y2="142"/><line x1="263.3" x2="263.3" y1="42" y2="142"/><line x1="287.7" x2="287.7" y1="42" y2="142"/>
    </g>
    <g font-size="2.4" fill="#555" text-anchor="end">
      <text x="18" y="43">100</text><text x="18" y="53">90</text><text x="18" y="63">80</text><text x="18" y="73">70</text><text x="18" y="83">60</text><text x="18" y="93">50</text><text x="18" y="103">40</text><text x="18" y="113">30</text><text x="18" y="123">20</text><text x="18" y="133">10</text><text x="18" y="143">0</text>
    </g>
    <g font-size="2.4" fill="#555" text-anchor="middle">
      <text x="32.2" y="148">JAN</text><text x="56.5" y="148">FEB</text><text x="80.8" y="148">MAR</text><text x="105.2" y="148">APR</text><text x="129.5" y="148">MAY</text><text x="153.8" y="148">JUN</text><text x="178.2" y="148">JUL</text><text x="202.5" y="148">AUG</text><text x="226.8" y="148">SEP</text><text x="251.2" y="148">OCT</text><text x="275.5" y="148">NOV</text><text x="299.8" y="148">DEC</text>
    </g>
    <polyline fill="none" stroke="var(--gray-line)" stroke-width=".7" points="20,132 44.3,112 68.7,122 93,92 117.3,82 141.7,102 166,92 190.3,102 214.7,82 239,62 263.3,72 287.7,82 312,62"/>
    <g fill="var(--gray-line)"><circle cx="20" cy="132" r="1"/><circle cx="44.3" cy="112" r="1"/><circle cx="68.7" cy="122" r="1"/><circle cx="93" cy="92" r="1"/><circle cx="117.3" cy="82" r="1"/><circle cx="141.7" cy="102" r="1"/><circle cx="166" cy="92" r="1"/><circle cx="190.3" cy="102" r="1"/><circle cx="214.7" cy="82" r="1"/><circle cx="239" cy="62" r="1"/><circle cx="263.3" cy="72" r="1"/><circle cx="287.7" cy="82" r="1"/><circle cx="312" cy="62" r="1"/></g>
    <polyline fill="none" stroke="var(--navy)" stroke-width=".8" points="20,102 44.3,92 68.7,102 93,72 117.3,72 141.7,82 166,72 190.3,72 214.7,55 239,52 263.3,52 287.7,55 312,52"/>
    <g fill="var(--navy)"><circle cx="20" cy="102" r="1.1"/><circle cx="44.3" cy="92" r="1.1"/><circle cx="68.7" cy="102" r="1.1"/><circle cx="93" cy="72" r="1.1"/><circle cx="117.3" cy="72" r="1.1"/><circle cx="141.7" cy="82" r="1.1"/><circle cx="166" cy="72" r="1.1"/><circle cx="190.3" cy="72" r="1.1"/><circle cx="214.7" cy="55" r="1.1"/><circle cx="239" cy="52" r="1.1"/><circle cx="263.3" cy="52" r="1.1"/><circle cx="287.7" cy="55" r="1.1"/><circle cx="312" cy="52" r="1.1"/></g>
    <g font-size="3" fill="#444"><circle cx="267" cy="37" r="1.6" fill="var(--gray-line)"/><text x="270" y="38">Sales</text><circle cx="291" cy="37" r="1.6" fill="var(--navy)"/><text x="294" y="38">Orders</text></g>
  </svg>
  <div class="brand foot on-light"><span class="brand-dot"></span>Velomar</div>
</section>

<!-- Stacked chart -->
<section class="slide light col-1 row-5">
  <h2 class="heading" style="left:13px;top:13px;color:var(--ink)">Heading Goes Here</h2>
  <div class="chart-label" style="left:12px">Stacked Chart</div>
  <svg class="layer" viewBox="0 0 325 183" role="img" aria-label="Stacked bar chart of monthly receipts, sales and orders">
    <g stroke="var(--grid)" stroke-width=".4">
      <line x1="22" x2="311" y1="43.5" y2="43.5"/><line x1="22" x2="311" y1="53.5" y2="53.5"/><line x1="22" x2="311" y1="63.5" y2="63.5"/><line x1="22" x2="311" y1="73.5" y2="73.5"/><line x1="22" x2="311" y1="83.5" y2="83.5"/><line x1="22" x2="311" y1="93.5" y2="93.5"/><line x1="22" x2="311" y1="103.5" y2="103.5"/><line x1="22" x2="311" y1="113.5" y2="113.5"/><line x1="22" x2="311" y1="123.5" y2="123.5"/><line x1="22" x2="311" y1="133.5" y2="133.5"/><line x1="22" x2="311" y1="143.5" y2="143.5"/>
    </g>
    <g font-size="2.4" fill="#555" text-anchor="end">
      <text x="19" y="44.5">100</text><text x="19" y="54.5">90</text><text x="19" y="64.5">80</text><text x="19" y="74.5">70</text><text x="19" y="84.5">60</text><text x="19" y="94.5">50</text><text x="19" y="104.5">40</text><text x="19" y="114.5">30</text><text x="19" y="124.5">20</text><text x="19" y="134.5">10</text><text x="19" y="144.5">0</text>
    </g>
    <g fill="var(--light-green)">
      <rect x="27" y="133.5" width="14" height="10"/><rect x="51.1" y="113.5" width="14" height="30"/><rect x="75.2" y="130.5" width="14" height="13"/><rect x="99.2" y="126.5" width="14" height="17"/><rect x="123.3" y="103.5" width="14" height="40"/><rect x="147.4" y="130.5" width="14" height="13"/><rect x="171.5" y="116.5" width="14" height="27"/><rect x="195.6" y="123.5" width="14" height="20"/><rect x="219.6" y="130.5" width="14" height="13"/><rect x="243.7" y="108.5" width="14" height="35"/><rect x="267.8" y="116.5" width="14" height="27"/><rect x="291.9" y="130.5" width="14" height="13"/>
    </g>
    <g fill="var(--green)">
      <rect x="27" y="123.5" width="14" height="10"/><rect x="51.1" y="83.5" width="14" height="30"/><rect x="75.2" y="116.5" width="14" height="14"/><rect x="99.2" y="60.5" width="14" height="66"/><rect x="123.3" y="83.5" width="14" height="20"/><rect x="171.5" y="90.5" width="14" height="26"/><rect x="195.6" y="103.5" width="14" height="20"/><rect x="219.6" y="116.5" width="14" height="14"/><rect x="243.7" y="73.5" width="14" height="35"/><rect x="267.8" y="90.5" width="14" height="26"/><rect x="291.9" y="116.5" width="14" height="14"/>
    </g>
    <g fill="var(--navy)">
      <rect x="27" y="113.5" width="14" height="10"/><rect x="51.1" y="53.5" width="14" height="30"/><rect x="75.2" y="83.5" width="14" height="33"/><rect x="99.2" y="43.5" width="14" height="17"/><rect x="123.3" y="63.5" width="14" height="20"/><rect x="147.4" y="116.5" width="14" height="14"/><rect x="171.5" y="63.5" width="14" height="27"/><rect x="195.6" y="53.5" width="14" height="50"/><rect x="219.6" y="93.5" width="14" height="23"/><rect x="267.8" y="63.5" width="14" height="27"/><rect x="291.9" y="103.5" width="14" height="13"/>
    </g>
    <g font-size="2.4" fill="#555" text-anchor="middle">
      <text x="34" y="149">JAN</text><text x="58.1" y="149">FEB</text><text x="82.2" y="149">MAR</text><text x="106.2" y="149">APR</text><text x="130.3" y="149">MAY</text><text x="154.4" y="149">JUN</text><text x="178.5" y="149">JUL</text><text x="202.6" y="149">AUG</text><text x="226.6" y="149">SEP</text><text x="250.7" y="149">OCT</text><text x="274.8" y="149">NOV</text><text x="298.9" y="149">DEC</text>
    </g>
    <g font-size="3" fill="#444"><circle cx="242" cy="38" r="1.6" fill="var(--navy)"/><text x="245" y="39">Receipts</text><circle cx="269" cy="38" r="1.6" fill="var(--green)"/><text x="272" y="39">Sales</text><circle cx="293" cy="38" r="1.6" fill="var(--light-green)"/><text x="296" y="39">Orders</text></g>
  </svg>
  <div class="brand foot on-light"><span class="brand-dot"></span>Velomar</div>
</section>

<!-- Process, navy -->
<section class="slide navy col-2 row-5">
  <h2 class="process-title g">PROCESS<small style="color:var(--white)">INFOGRAPHIC</small></h2>
  <svg class="layer" viewBox="0 0 325 183" aria-label="Four-step process" role="img">
    <defs>
      <marker id="head-green" viewBox="0 0 6 6" refX="3" refY="3" markerWidth="4" markerHeight="4" orient="auto"><path d="M0 0L6 3L0 6Z" fill="var(--green)"/></marker>
      <marker id="head-white" viewBox="0 0 6 6" refX="3" refY="3" markerWidth="4" markerHeight="4" orient="auto"><path d="M0 0L6 3L0 6Z" fill="var(--white)"/></marker>
    </defs>
    <path d="M84 80 Q84 65 101 65 Q118 65 121 76" fill="none" stroke="var(--green)" stroke-width="1.6" marker-end="url(#head-green)"/>
    <path d="M143 80 Q143 65 160 65 Q177 65 180 76" fill="none" stroke="var(--white)" stroke-width="1.6" marker-end="url(#head-white)"/>
    <path d="M202 80 Q202 65 219 65 Q236 65 239 76" fill="none" stroke="var(--green)" stroke-width="1.6" marker-end="url(#head-green)"/>
    <rect x="45" y="81" width="59" height="28" fill="var(--green)"/>
    <rect x="104" y="81" width="59" height="28" fill="var(--white)"/>
    <rect x="163" y="81" width="59" height="28" fill="var(--green)"/>
    <rect x="222" y="81" width="56" height="28" fill="var(--white)"/>
    <circle cx="104" cy="95" r="5" fill="var(--green)"/>
    <circle cx="163" cy="95" r="5" fill="var(--white)"/>
    <circle cx="222" cy="95" r="5" fill="var(--green)"/>
    <circle cx="278" cy="95" r="5" fill="var(--white)"/>
    <circle cx="45" cy="95" r="4.5" fill="var(--navy)"/>
    <g font-size="11" font-weight="500" text-anchor="middle">
      <text x="66" y="99" fill="var(--white)">01</text><text x="132" y="99" fill="var(--navy)">02</text><text x="189" y="99" fill="var(--white)">03</text><text x="250" y="99" fill="var(--navy)">04</text>
    </g>
    <g text-anchor="middle" fill="var(--white)">
      <g font-size="3.8" font-weight="600"><text x="73" y="119">LOREM IPSUM</text><text x="130" y="119">LOREM IPSUM</text><text x="189" y="119">LOREM IPSUM</text><text x="247" y="119">LOREM IPSUM</text></g>
      <g font-size="2.7">
        <text x="73" y="123.5">Lorem ipsum dolor</text><text x="73" y="127">sit amet consectetur</text><text x="73" y="130.5">adipiscing elit.</text><text x="73" y="134">Duis elit sapien.</text>
        <text x="130" y="123.5">Lorem ipsum dolor</text><text x="130" y="127">sit amet consectetur</text><text x="130" y="130.5">adipiscing elit.</text><text x="130" y="134">Duis elit sapien.</text>
        <text x="189" y="123.5">Lorem ipsum dolor</text><text x="189" y="127">sit amet consectetur</text><text x="189" y="130.5">adipiscing elit.</text><text x="189" y="134">Duis elit sapien.</text>
        <text x="247" y="123.5">Lorem ipsum dolor</text><text x="247" y="127">sit amet consectetur</text><text x="247" y="130.5">adipiscing elit.</text><text x="247" y="134">Duis elit sapien.</text>
      </g>
    </g>
  </svg>
  <div class="brand foot on-navy"><span class="brand-dot"></span>Velomar</div>
</section>

<!-- Process, white -->
<section class="slide light col-3 row-5">
  <h2 class="process-title" style="color:var(--navy)">PROCESS<small>INFOGRAPHIC</small></h2>
  <svg class="layer" viewBox="0 0 325 183" aria-label="Four-step process" role="img">
    <g fill="none" stroke="var(--teal)" stroke-width=".9">
      <polyline points="72,76 72,64 129,64 129,76"/>
      <polyline points="135,76 135,64 191,64 191,76"/>
      <polyline points="197,76 197,64 253,64 253,76"/>
    </g>
    <g fill="var(--card)">
      <rect x="46" y="100" width="46" height="52"/><rect x="109" y="100" width="46" height="52"/><rect x="171" y="100" width="46" height="52"/><rect x="233" y="100" width="46" height="52"/>
    </g>
    <g stroke-width="2.5">
      <polygon points="94,96 81.5,74.4 56.5,74.4 44,96 56.5,117.6 81.5,117.6" fill="var(--navy)" stroke="#c7cfdd"/>
      <polygon points="157,96 144.5,74.4 119.5,74.4 107,96 119.5,117.6 144.5,117.6" fill="var(--green)" stroke="#d6e8bd"/>
      <polygon points="219,96 206.5,74.4 181.5,74.4 169,96 181.5,117.6 206.5,117.6" fill="var(--navy)" stroke="#c7cfdd"/>
      <polygon points="281,96 268.5,74.4 243.5,74.4 231,96 243.5,117.6 268.5,117.6" fill="var(--green)" stroke="#d6e8bd"/>
    </g>
    <g font-size="15" font-weight="500" fill="var(--white)" text-anchor="middle">
      <text x="69" y="101.5">01</text><text x="132" y="101.5">02</text><text x="194" y="101.5">03</text><text x="256" y="101.5">04</text>
    </g>
    <g text-anchor="middle">
      <g font-size="3.8" font-weight="600" fill="var(--navy)"><text x="69" y="128">LOREM IPSUM</text><text x="132" y="128">LOREM IPSUM</text><text x="194" y="128">LOREM IPSUM</text><text x="256" y="128">LOREM IPSUM</text></g>
      <g font-size="2.6" fill="#8a8a8a">
        <text x="69" y="132.5">Lorem ipsum dolor</text><text x="69" y="136">sit amet consectetur</text><text x="69" y="139.5">adipiscing elit.</text><text x="69" y="143">Duis elit sapien.</text>
        <text x="132" y="132.5">Lorem ipsum dolor</text><text x="132" y="136">sit amet consectetur</text><text x="132" y="139.5">adipiscing elit.</text><text x="132" y="143">Duis elit sapien.</text>
        <text x="194" y="132.5">Lorem ipsum dolor</text><text x="194" y="136">sit amet consectetur</text><text x="194" y="139.5">adipiscing elit.</text><text x="194" y="143">Duis elit sapien.</text>
        <text x="256" y="132.5">Lorem ipsum dolor</text><text x="256" y="136">sit amet consectetur</text><text x="256" y="139.5">adipiscing elit.</text><text x="256" y="143">Duis elit sapien.</text>
      </g>
    </g>
  </svg>
  <div class="brand foot on-light"><span class="brand-dot"></span>Velomar</div>
</section>

</body>
</html>
```